Firm Stationery Design

I need a design for stationery, including: Stationery First Page, Stationery Second Sheet, Envelope, Mailing Label for Flat Envelopes, and Business Cards

```html
<!DOCTYPE html>
<html lang="en">
<head>
<meta charset="utf-8">
<title>Marlow Legal LLC — Stationery</title>
<link rel="stylesheet" href="https://fonts.googleapis.com/css2?family=Montserrat:wght@500;700;800&family=Open+Sans:wght@400;600&display=swap">
<style>
  :root {
    --ink: #1b1b1b;
    --ink-deep: #0e0e0e;
    --orange: #f5a01c;
    --paper: #ffffff;
    --paper-soft: #f3f3f3;
    --stage: #a4a4a4;
    --stage-light: #b4b2b3;
    --rule: #3a3a3a;
    --muted: #555555;
    --pattern-dark: #151515;
    --pattern-mid: #4a4a4a;
    --pattern-light: #8a8a8a;
  }
  * { box-sizing: border-box; margin: 0; padding: 0; }
  html, body { width: 1200px; height: 957px; overflow: hidden; }
  body {
    position: relative;
    background: var(--stage);
    font-family: "Open Sans", Arial, sans-serif;
    color: var(--ink);
  }
  .stage-panel { position: absolute; left: 650px; top: 0; width: 550px; height: 523px; background: var(--stage-light); }
  .notebook-zone { position: absolute; left: 256px; top: 287px; width: 377px; height: 236px; border: 1px solid #989898; }

  .item { position: absolute; box-shadow: 1px 2px 4px rgba(0,0,0,.3); overflow: hidden; }
  .dark { background: var(--ink); color: var(--paper); }
  .light { background: var(--paper); }

  .pattern {
    position: absolute; inset: 0;
    background: linear-gradient(100deg, var(--pattern-dark) 0%, var(--pattern-dark) 35%, var(--pattern-mid) 70%, var(--pattern-light) 100%);
  }
  .pattern.fade-left { background: linear-gradient(80deg, var(--pattern-mid) 0%, var(--pattern-dark) 35%, var(--pattern-dark) 55%, var(--pattern-mid) 80%, var(--pattern-light) 100%); }

  /* wordmark */
  .mark { position: absolute; display: flex; align-items: center; gap: .35em; font-family: "Montserrat", Arial, sans-serif; font-weight: 800; line-height: 1.02; letter-spacing: .02em; white-space: nowrap; }
  .mark-square { width: 1.1em; height: 1.1em; background: var(--orange); flex: none; }
  .mark-name { color: var(--ink); }
  .dark .mark-name, .on-dark .mark-name { color: var(--paper); }

  .contact { position: absolute; font-size: 5px; line-height: 1.45; white-space: nowrap; }
  .contact-row { display: flex; align-items: center; gap: 2px; }
  .contact svg { width: 1em; height: 1em; flex: none; }
  .divider { position: absolute; width: 1px; background: var(--orange); }

  /* business card front */
  .card-front { left: 77px; top: 77px; width: 166px; height: 95px; }
  .card-front .mark { left: 40px; top: 34px; font-size: 13px; }

  /* business card back */
  .card-back { left: 77px; top: 185px; width: 166px; height: 94px; background: var(--ink); color: var(--paper); }
  .card-back .mark { left: 8px; top: 8px; font-size: 8px; }
  .card-holder { position: absolute; right: 6px; top: 8px; text-align: right; font-family: "Montserrat", Arial, sans-serif; }
  .card-holder .holder-name { color: var(--orange); font-weight: 700; font-size: 7px; letter-spacing: .02em; }
  .card-holder .holder-role { font-size: 5px; font-weight: 500; }
  .card-back .contact { left: 8px; top: 52px; font-family: "Montserrat", Arial, sans-serif; }
  .card-back .accent-block { position: absolute; right: 0; bottom: 0; width: 62px; height: 60px; background: var(--paper); }
  .card-back .accent-block::after { content: ""; position: absolute; right: 0; top: 0; width: 30px; height: 60px; background: var(--orange); }

  /* letterhead */
  .letterhead { left: 257px; top: 78px; width: 141px; height: 200px; padding: 10px 12px; }
  .letterhead .mark { left: 12px; top: 11px; font-size: 6px; }
  .letterhead .divider { left: 92px; top: 10px; height: 20px; }
  .letterhead .contact { left: 95px; top: 10px; font-size: 2.6px; }
  .letter-body { position: absolute; left: 13px; top: 52px; width: 116px; font-size: 2.6px; line-height: 1.55; color: var(--muted); }
  .letter-body .recipient { font-weight: 600; color: var(--ink); margin-bottom: 12px; }
  .letter-body p { margin-bottom: 5px; }
  .letter-body .sign { margin-top: 12px; }

  /* DL envelope front / back */
  .envelope-front { left: 412px; top: 79px; width: 209px; height: 90px; }
  .envelope-front .mark { left: 8px; top: 9px; font-size: 6px; }
  .envelope-front .divider { left: 54px; top: 8px; height: 14px; }
  .envelope-front .contact { left: 58px; top: 9px; font-size: 3.2px; }
  .envelope-back { left: 409px; top: 185px; width: 210px; height: 92px; }
  .envelope-back svg.flap { position: absolute; left: 0; top: 0; width: 210px; height: 34px; }
  .envelope-back .mark { left: 84px; top: 11px; font-size: 7px; }

  /* notebook cover */
  .notebook-cover { left: 78px; top: 309px; width: 140px; height: 200px; }
  .notebook-cover .mark { left: 22px; top: 82px; font-size: 15px; }
  .binding { position: absolute; left: -4px; top: 4px; width: 10px; height: 192px; background: repeating-linear-gradient(180deg, var(--ink-deep) 0 3px, transparent 3px 11.5px); }

  /* notebook spread */
  .notebook-page { top: 310px; width: 140px; height: 197px; background: var(--paper-soft); padding: 0 8px; }
  .page-left { left: 301px; }
  .page-right { left: 442px; }
  .notebook-page .mark { left: 7px; top: 6px; font-size: 5px; }
  .page-date { position: absolute; right: 6px; top: 14px; font-size: 4px; color: var(--muted); }
  .page-lines { position: absolute; left: 7px; right: 6px; top: 35px; height: 160px; background: repeating-linear-gradient(180deg, transparent 0 7px, var(--rule) 7px 7.6px); }
  .spiral { position: absolute; left: 437px; top: 312px; width: 8px; height: 193px; background: repeating-linear-gradient(180deg, var(--ink-deep) 0 2px, transparent 2px 6px); }

  /* presentation folder */
  .folder-front { left: 700px; top: 70px; width: 175px; height: 225px; }
  .folder-front .mark { left: 18px; top: 70px; font-size: 17px; }
  .folder-front .contact { left: 14px; top: 188px; font-size: 5.5px; font-family: "Montserrat", Arial, sans-serif; white-space: normal; width: 150px; }
  .folder-back { left: 880px; top: 70px; width: 175px; height: 225px; }
  .folder-back .mark { left: 30px; top: 60px; font-size: 13px; }

  .folder-open { left: 700px; top: 315px; width: 380px; height: 180px; background: var(--paper-soft); }
  .folder-open .panel-left { position: absolute; left: 0; top: 0; width: 190px; height: 180px; background: linear-gradient(90deg, #ffffff, #e2e2e2); }
  .folder-open .pocket-left { position: absolute; left: 0; bottom: 0; width: 190px; height: 55px; background: var(--ink); }
  .folder-open .inner-sheet { position: absolute; left: 220px; top: 12px; width: 120px; height: 150px; background: var(--paper); box-shadow: 0 1px 3px rgba(0,0,0,.25); }
  .folder-open .inner-sheet .mark { left: 10px; top: 10px; font-size: 5px; }
  .folder-open .inner-sheet .sheet-text { position: absolute; left: 10px; top: 36px; width: 100px; font-size: 2.8px; color: var(--muted); line-height: 1.5; }
  .folder-open .pocket-right { position: absolute; left: 190px; bottom: 0; width: 190px; height: 65px; background: var(--orange); }

  /* C4 envelope / second sheet */
  .envelope-large { left: 78px; top: 586px; width: 356px; height: 267px; }
  .envelope-large .mark { left: 25px; top: 27px; font-size: 12px; }
  .envelope-large .divider { left: 112px; top: 24px; height: 36px; }
  .envelope-large .address { position: absolute; left: 121px; top: 30px; font-size: 9px; line-height: 1.4; color: var(--muted); }

  .mailing-label { left: 480px; top: 586px; width: 198px; height: 264px; }
  .mailing-label .mark { left: 15px; top: 20px; font-size: 9px; }
  .mailing-label .divider { left: 80px; top: 16px; height: 26px; }
  .mailing-label .address { position: absolute; left: 86px; top: 19px; font-size: 6.5px; line-height: 1.4; color: var(--muted); }

  /* compliments slips */
  .slip-dark { left: 810px; top: 571px; width: 275px; height: 130px; }
  .slip-dark .mark { left: 88px; top: 45px; font-size: 17px; }
  .slip-light { left: 808px; top: 733px; width: 275px; height: 130px; }
  .slip-light .mark { left: 14px; top: 45px; font-size: 14px; }
  .slip-light .contact { left: 203px; top: 32px; font-size: 5px; }
  .slip-light .compliments { position: absolute; right: 12px; bottom: 10px; font-size: 11px; }
  .slip-light .compliments em { font-style: normal; color: var(--orange); }
</style>
</head>
<body>
  <div class="stage-panel"></div>
  <div class="notebook-zone"></div>

  <!-- business card, front -->
  <section class="item dark card-front">
    <div class="pattern" role="img" aria-label="Repeating chevron pattern in black and grey"></div>
    <div class="mark on-dark"><span class="mark-square"></span><span class="mark-name">MARLOW<br>LEGAL LLC</span></div>
  </section>

  <!-- business card, back -->
  <section class="item card-back">
    <div class="mark on-dark"><span class="mark-name">MARLOW<br>LEGAL LLC</span></div>
    <div class="card-holder">
      <div class="holder-name">DANIEL REYES</div>
      <div class="holder-role">Managing Director</div>
    </div>
    <div class="contact">
      <div>Your address, City</div>
      <div>State, Zip 1234</div>
      <div class="contact-row"><svg viewBox="0 0 10 10"><path d="M2 1h2l1 2-1 1a6 6 0 0 0 2 2l1-1 2 1v2a1 1 0 0 1-1 1A8 8 0 0 1 1 2a1 1 0 0 1 1-1z" fill="#f5a01c"/></svg>123 456 789</div>
      <div class="contact-row"><svg viewBox="0 0 10 10"><rect x="1" y="2" width="8" height="6" fill="#f5a01c"/><path d="M1 2l4 3 4-3" stroke="#1b1b1b" fill="none"/></svg>info@marlowlegal.com</div>
      <div class="contact-row"><svg viewBox="0 0 10 10"><circle cx="5" cy="5" r="4" fill="#f5a01c"/></svg>www.marlowlegal.com</div>
    </div>
    <div class="accent-block"></div>
  </section>

  <!-- letterhead, first page -->
  <section class="item light letterhead">
    <div class="mark"><span class="mark-name">MARLOW<br>LEGAL LLC</span></div>
    <span class="divider"></span>
    <div class="contact">
      <div>Your address, City</div>
      <div>State, Zip 1234</div>
      <div>123 456 789</div>
      <div>info@marlowlegal.com</div>
      <div>www.marlowlegal.com</div>
    </div>
    <div class="letter-body">
      <div class="recipient">PRIYA SANDOVAL<br><span style="font-weight:400">Chief Executive Officer<br>City State, Zip Code</span></div>
      <p>Thank you for meeting with our team last week. We have reviewed the documents you shared and prepared a short summary of next steps for your matter.</p>
      <p>Our attorneys will contact you to confirm the schedule and answer any questions about the filing process and expected costs.</p>
      <p>Please keep this letter with your records and call us if anything changes before our next meeting.</p>
      <div class="sign">Sincerely,<br><br>Daniel Reyes</div>
    </div>
  </section>

  <!-- DL envelope, front -->
  <section class="item light envelope-front">
    <div class="mark"><span class="mark-name">MARLOW<br>LEGAL LLC</span></div>
    <span class="divider"></span>
    <div class="contact"><div>Your address, City</div><div>State, Zip 1234</div></div>
  </section>

  <!-- DL envelope, back -->
  <section class="item light envelope-back">
    <svg class="flap" viewBox="0 0 210 34" aria-hidden="true"><path d="M0 0h210l-6 24a10 10 0 0 1-10 10H16A10 10 0 0 1 6 24z" fill="#1b1b1b"/></svg>
    <div class="mark on-dark"><span class="mark-square"></span></div>
  </section>

  <!-- notebook cover -->
  <section class="item dark notebook-cover">
    <div class="pattern fade-left" role="img" aria-label="Repeating chevron pattern in black and grey"></div>
    <div class="mark on-dark"><span class="mark-name">MARLOW<br>LEGAL LLC</span></div>
    <div class="binding"></div>
  </section>

  <!-- notebook spread -->
  <section class="item notebook-page page-left">
    <div class="mark"><span class="mark-name">MARLOW<br>LEGAL LLC</span></div>
    <div class="page-date">Date....../....../......</div>
    <div class="page-lines"></div>
  </section>
  <section class="item notebook-page page-right">
    <div class="mark"><span class="mark-name">MARLOW<br>LEGAL LLC</span></div>
    <div class="page-date">Date....../....../......</div>
    <div class="page-lines"></div>
  </section>
  <div class="spiral"></div>

  <!-- presentation folder -->
  <section class="item dark folder-front">
    <div class="mark on-dark"><span class="mark-square"></span><span class="mark-name">MARLOW<br>LEGAL LLC</span></div>
    <div class="contact">Your address, City State, Zip 1234<br>123 456 789 · info@marlowlegal.com · www.marlowlegal.com</div>
  </section>
  <section class="item dark folder-back">
    <div class="pattern" role="img" aria-label="Repeating chevron pattern in black and grey"></div>
    <div class="mark on-dark"><span class="mark-name">MARLOW<br>LEGAL LLC</span></div>
  </section>
  <section class="item folder-open">
    <div class="panel-left"></div>
    <div class="pocket-left"></div>
    <div class="inner-sheet">
      <div class="mark"><span class="mark-name">MARLOW<br>LEGAL LLC</span></div>
      <div class="sheet-text">Dear client, please find our documents enclosed.</div>
    </div>
    <div class="pocket-right"></div>
  </section>

  <!-- large envelope -->
  <section class="item light envelope-large">
    <div class="mark"><span class="mark-name">MARLOW<br>LEGAL LLC</span></div>
    <span class="divider"></span>
    <div class="address">Your address, City<br>State, Zip 1234</div>
  </section>

  <!-- second sheet -->
  <section class="item light mailing-label">
    <div class="mark"><span class="mark-name">MARLOW<br>LEGAL LLC</span></div>
    <span class="divider"></span>
    <div class="address">Your address, City<br>State, Zip 1234</div>
  </section>

  <!-- compliments slips -->
  <section class="item dark slip-dark">
    <div class="pattern fade-left" role="img" aria-label="Repeating chevron pattern in black and grey"></div>
    <div class="mark on-dark"><span class="mark-square"></span><span class="mark-name">MARLOW<br>LEGAL LLC</span></div>
  </section>
  <section class="item light slip-light">
    <div class="mark"><span class="mark-square"></span><span class="mark-name">MARLOW<br>LEGAL LLC</span></div>
    <div class="contact">
      <div>Your address, City</div>
      <div>State, Zip 1234</div>
      <div style="margin-top:3px">123 456 789</div>
      <div>info@marlowlegal.com</div>
      <div>www.marlowlegal.com</div>
    </div>
    <div class="compliments">with <em>compliments</em></div>
  </section>
</body>
</html>
```